Coastline Premier Retreats Business Card Design

Design a business card for Coastline Premier Retreats. Look at the website for colors and reference. Card should have logo, name, title, office number, mobile number, email, URL and a tagline like, "Luxury Hotel & Resort Email Marketing" (This might change).

https://www.coastlinepremierretreats.example

The rest I will leave up to your imagination.

Contact Information for Business Card

Logo, name, title, office number, mobile number, email, URL and a tagline like, "Luxury Hotel & Resort Email Marketing" (This might change).

```html
<!DOCTYPE html>
<html lang="en">
<head>
<meta charset="utf-8">
<title>Coastline Premier Retreats – Business Card</title>
<link href="https://fonts.googleapis.com/css2?family=Poppins:wght@400;500;600;700&display=swap" rel="stylesheet">
<style>
  :root {
    --stage: #2b2b2d;
    --card-white: #ffffff;
    --card-black: #1b1c1e;
    --pattern: #242528;
    --ink: #111111;
    --orange: #f07c12;
    --rule: #9a9a9a;
  }
  * { margin: 0; padding: 0; box-sizing: border-box; }
  html, body { width: 1200px; height: 1108px; overflow: hidden; }
  body {
    background: var(--stage);
    font-family: "Poppins", sans-serif;
    position: relative;
  }
  .card {
    position: absolute;
    top: 214px;
    width: 410px;
    height: 680px;
    border-radius: 22px;
    overflow: hidden;
  }
  .card-front { left: 150px; background: var(--card-white); color: var(--ink); text-align: center; }
  .card-back { left: 640px; background: var(--card-black); }

  .brand-name {
    position: absolute;
    top: 150px; left: 0; right: 0;
    font-weight: 700;
    font-size: 30px;
    line-height: 1.15;
    letter-spacing: 1px;
    text-transform: uppercase;
    color: var(--ink);
  }
  .person { position: absolute; top: 372px; left: 0; right: 0; }
  .person-name { font-weight: 600; font-size: 30px; letter-spacing: 0.5px; text-transform: uppercase; line-height: 1.1; }
  .person-title { color: var(--orange); font-size: 20px; letter-spacing: 0.5px; text-transform: uppercase; margin-top: 2px; }

  .icon-row {
    position: absolute; top: 468px; left: 40px; right: 40px;
    display: flex; align-items: center; gap: 8px;
  }
  .icon-row .rule { flex: 1; height: 1px; background: var(--rule); }
  .icon-tile {
    width: 30px; height: 30px; border-radius: 5px; background: var(--orange);
    display: flex; align-items: center; justify-content: center;
  }
  .contact { position: absolute; top: 512px; left: 0; right: 0; font-size: 17px; line-height: 1.55; }
  .divider { position: absolute; top: 612px; left: 60px; right: 60px; height: 1px; background: var(--rule); }
  .tagline { position: absolute; top: 630px; left: 0; right: 0; color: var(--orange); font-weight: 600; font-size: 17px; }

  .back-pattern { position: absolute; inset: 0; background: linear-gradient(160deg, var(--pattern), var(--card-black)); }
  .back-brand {
    position: absolute; top: 50%; left: 0; right: 0; transform: translateY(-50%);
    text-align: center; color: #ffffff; font-weight: 700; font-size: 28px;
    line-height: 1.15; letter-spacing: 1px; text-transform: uppercase;
  }
</style>
</head>
<body>
  <section class="card card-front">
    <div class="brand-name">Coastline<br>Premier Retreats</div>
    <div class="person">
      <div class="person-name">Daniel Harper</div>
      <div class="person-title">Managing Director</div>
    </div>
    <div class="icon-row">
      <span class="rule"></span>
      <span class="icon-tile">
        <svg width="18" height="18" viewBox="0 0 24 24" aria-hidden="true"><path fill="#fff" d="M6.6 10.8a15.1 15.1 0 0 0 6.6 6.6l2.2-2.2a1 1 0 0 1 1-.25 11.4 11.4 0 0 0 3.6.57 1 1 0 0 1 1 1V20a1 1 0 0 1-1 1A17 17 0 0 1 3 4a1 1 0 0 1 1-1h3.5a1 1 0 0 1 1 1c0 1.25.2 2.45.57 3.57a1 1 0 0 1-.25 1z"/></svg>
      </span>
      <span class="icon-tile">
        <svg width="18" height="18" viewBox="0 0 24 24" aria-hidden="true"><rect x="3" y="6" width="18" height="12" fill="none" stroke="#fff" stroke-width="2"/><path d="M3 6l9 7 9-7" fill="none" stroke="#fff" stroke-width="2"/></svg>
      </span>
      <span class="icon-tile">
        <svg width="18" height="18" viewBox="0 0 24 24" aria-hidden="true"><circle cx="12" cy="12" r="9" fill="none" stroke="#fff" stroke-width="2"/><path d="M3 12h18M12 3c3 3 3 15 0 18M12 3c-3 3-3 15 0 18" fill="none" stroke="#fff" stroke-width="1.5"/></svg>
      </span>
      <span class="rule"></span>
    </div>
    <div class="contact">
      <div>044-555 010 234</div>
      <div>info@coastlinemail.example</div>
      <div>www.coastlinepremierretreats.example</div>
    </div>
    <div class="divider"></div>
    <div class="tagline">Luxury Hotel &amp; Resort Email Marketing</div>
  </section>

  <section class="card card-back">
    <div class="back-pattern" role="img" aria-label="Tonal embossed pattern of repeated brand name across the dark card"></div>
    <div class="back-brand">Coastline<br>Premier Retreats</div>
  </section>
</body>
</html>
```